Stationery Design

Need a stationery design for an established accounting firm based in London, England.

The company’s name is ‘Marcus Thorne’. We provide a broad range of bookkeeping, accounting, audit, tax and business services to a wide range of clients (ie, individuals, company, partnerships, etc).

The stationary design needs to show strength and trust and should be clean, corporate and professional.

Only 2 colours must be used as noted on the logo.

The fonts are in Optima

We need the following:

#1: Business Cards (design on 2 sides)
#2: Letterhead (word format) and can be sent to printers
#3: Continuation sheets (word format) and can be sent to printers
#4: Sales invoice template (word format) and can be sent to printers
#5: Report Cover front and back for binding,
#6: Complimentary Slips,
#7: Legal corners with our logo only
#7: Email signature templates

I have attached my company's logo in various file formats

We also need to have our accountancy association’s logo and this must be in the same colour as the dark blue. This IFRB logo must be at least 8mm square (can be larger). I have attached the IFRB logo in various file formats

I have also attached other information that you will need for the letter head and invoice templates

I have also attached our old letterhead, fee note template for reference
Updates

Dear Designers - I have increased the budget

Dear Designers - I have read your comments on the fact that the prize does not reflect the work. Thank you and I appreciate your comments. Unfortunately, I am a start up and my budget is limited. As an Alternative, I have reduced the work that I am asking for to the following items and I hope you can assist: #1: Business Cards (design on 2 sides) #2: Letterhead (word format) and can be sent to printers #3: Report Cover front and back for binding, #4: Email signature templates Regards

Industry/Entity Type

Accounting

```html
<!DOCTYPE html>
<html lang="en">
<head>
<meta charset="utf-8">
<title>Marcus Thorne Accountants – Report Cover</title>
<link rel="stylesheet" href="https://fonts.googleapis.com/css2?family=Marcellus&family=Raleway:wght@200&display=swap">
<style>
  :root {
    --navy: #12406a;
    --navy-light: #1d5286;
    --white: #ffffff;
    --page-bg: #f4f4f4;
    --backdrop: #a9bed4;
    --soft-white: rgba(255,255,255,0.82);
  }
  * { margin: 0; padding: 0; box-sizing: border-box; }
  html, body { width: 1200px; height: 1000px; overflow: hidden; }
  body {
    background: var(--backdrop);
    font-family: "Marcellus", serif;
    position: relative;
  }
  .cover-spread {
    position: absolute;
    left: 180px; top: 203px;
    width: 840px; height: 594px;
    display: flex;
    box-shadow: 0 18px 40px rgba(20,40,70,0.25);
  }
  .cover { position: relative; width: 420px; height: 594px; overflow: hidden; }

  /* Back cover */
  .back { background: var(--navy); }
  .back-decor {
    position: absolute; left: 0; top: 0; width: 420px; height: 480px;
    background: linear-gradient(160deg, var(--page-bg) 0%, #c9d3de 22%, var(--navy) 60%);
  }
  .back-footer {
    position: absolute; left: 24px; right: 24px; top: 496px;
    border-top: 1px solid rgba(255,255,255,0.35);
    padding-top: 12px;
    display: grid;
    grid-template-columns: 130px 110px 1fr;
    gap: 10px;
    color: var(--soft-white);
    font-size: 6.4px;
    line-height: 1.45;
  }
  .footer-name {
    font-size: 11px; letter-spacing: 0.06em; color: var(--white);
    text-transform: uppercase; line-height: 1.1;
  }
  .footer-sub {
    font-size: 5.5px; letter-spacing: 0.3em; color: var(--white);
    text-transform: uppercase; margin: 1px 0 6px 24px;
  }
  .footer-contact { padding-top: 26px; }
  .footer-legal { font-size: 6px; }

  /* Front cover */
  .front { background: var(--page-bg); }
  .front-decor {
    position: absolute; left: 0; top: 58px; width: 322px; height: 420px;
    background: linear-gradient(170deg, var(--navy-light) 0%, var(--navy) 70%);
  }
  .brand {
    position: absolute; right: 30px; top: 14px;
    display: flex; align-items: flex-start; gap: 7px;
    color: var(--navy);
  }
  .brand-mark { width: 13px; height: 13px; background: var(--navy); margin-top: 2px; }
  .brand-name { font-size: 15px; letter-spacing: 0.04em; text-transform: uppercase; line-height: 1; }
  .brand-sub {
    font-size: 6px; letter-spacing: 0.32em; text-transform: uppercase;
    text-align: right; margin-top: 3px;
  }
  .report-title {
    position: absolute; right: 116px; top: 82px;
    text-align: right; color: var(--white);
    font-family: "Raleway", sans-serif; font-weight: 200;
    font-size: 20px; letter-spacing: 0.04em; line-height: 1.15;
  }
</style>
</head>
<body>
  <main class="cover-spread">
    <section class="cover back" aria-label="Back cover">
      <div class="back-decor" role="img" aria-label="Decorative sweeping band graphic in white and navy"></div>
      <div class="back-footer">
        <div class="footer-address">
          <div class="footer-name">Marcus Thorne</div>
          <div class="footer-sub">Accountants</div>
          12 Kestrel Court,<br>
          Elmridge Business Park,<br>
          Fenwick Road, Wealdstone,<br>
          Middlesex HA3 7QT
        </div>
        <div class="footer-contact">
          T: 020 7946 0132<br>
          F: 020 7946 0178<br>
          E: office@marcusthorne.co.uk<br>
          W: www.marcusthorne.co.uk
        </div>
        <div class="footer-legal">
          Company registered in England and Wales No. 08731652. Registered to carry on audit work in the United Kingdom and regulated for a range of investment business activities by the Institute of Financial Reporting Bodies.
        </div>
      </div>
    </section>

    <section class="cover front" aria-label="Front cover">
      <div class="front-decor" role="img" aria-label="Decorative navy panel with angled frame"></div>
      <div class="brand">
        <span class="brand-mark"></span>
        <div>
          <div class="brand-name">Marcus Thorne</div>
          <div class="brand-sub">Accountants</div>
        </div>
      </div>
      <h1 class="report-title">ANNUAL REPORT<br>-2014-</h1>
    </section>
  </main>
</body>
</html>
```